Software allocation system needs a business card design

We need a business card designed for our software platform - www.tallivo.com.au

At the moment the logo and website is all black and white, we are happy for suggestions on implementing some colour throughout either the logo or business card.

Industry/Entity Type

Software

Font styles to use
Sans Serif

Colors

Designer to choose colors to be used in the design.

```html
<!DOCTYPE html>
<html lang="en">
<head>
<meta charset="utf-8">
<title>Tallivo business card</title>
<link rel="stylesheet" href="https://fonts.googleapis.com/css2?family=Questrial&display=swap">
<style>
  :root {
    --brand-orange: #e06c10;
    --card-white: #f4f4f4;
    --ink: #3a3a3a;
    --backdrop: #e6e4e1;
  }
  * { margin: 0; padding: 0; box-sizing: border-box; }
  html, body { width: 1200px; height: 900px; overflow: hidden; }
  body {
    background: var(--backdrop);
    font-family: "Questrial", "Helvetica Neue", Arial, sans-serif;
    position: relative;
  }
  .card {
    position: absolute;
    left: 320px;
    width: 560px;
    height: 330px;
    border-radius: 4px;
    box-shadow: 0 6px 18px rgba(0,0,0,0.12);
    overflow: hidden;
  }
  .card-front { top: 100px; background: var(--brand-orange); display: flex; align-items: center; justify-content: center; }
  .card-back { top: 470px; background: var(--card-white); }
  .wordmark {
    font-size: 40px;
    letter-spacing: 6px;
    font-weight: 400;
    color: #ffffff;
    display: flex;
    align-items: center;
    gap: 12px;
  }
  .wordmark-dot { width: 14px; height: 14px; border-radius: 50%; background: #ffffff; }
  .card-back .wordmark { position: absolute; left: 40px; top: 58px; color: var(--brand-orange); font-size: 34px; letter-spacing: 5px; }
  .card-back .wordmark-dot { background: var(--brand-orange); width: 12px; height: 12px; }
  .contact-block { position: absolute; left: 230px; top: 122px; color: var(--ink); }
  .person-name { font-size: 14px; letter-spacing: 3.2px; font-weight: 400; }
  .person-role { font-size: 11px; letter-spacing: 2px; color: var(--brand-orange); margin-top: 3px; margin-bottom: 20px; }
  .contact-list { list-style: none; }
  .contact-list li { display: flex; align-items: center; gap: 10px; font-size: 12px; letter-spacing: 1px; line-height: 22px; white-space: nowrap; }
  .contact-list svg { width: 12px; height: 12px; flex: none; }
</style>
</head>
<body>
  <section class="card card-front" aria-label="Card front">
    <div class="wordmark"><span class="wordmark-dot"></span>TALLIVO</div>
  </section>

  <section class="card card-back" aria-label="Card back">
    <div class="wordmark"><span class="wordmark-dot"></span>TALLIVO</div>

    <div class="contact-block">
      <h1 class="person-name">LENA BRANDT</h1>
      <p class="person-role">CEO</p>
      <ul class="contact-list">
        <li>
          <svg viewBox="0 0 12 12"><path d="M6 1a3.5 3.5 0 0 0-3.5 3.5C2.5 7.5 6 11 6 11s3.5-3.5 3.5-6.5A3.5 3.5 0 0 0 6 1z" fill="var(--brand-orange)"/><circle cx="6" cy="4.5" r="1.2" fill="#fff"/></svg>
          Lindenweg 7, 4051 Basel, Switzerland
        </li>
        <li>
          <svg viewBox="0 0 12 12"><path d="M3 1h2l1 3-1.5 1a6 6 0 0 0 2.5 2.5L8 6l3 1v2a1.5 1.5 0 0 1-1.5 1.5C5 10.5 1.5 7 1.5 2.5A1.5 1.5 0 0 1 3 1z" fill="var(--brand-orange)"/></svg>
          +41 61 310 48 26
        </li>
        <li>
          <svg viewBox="0 0 12 12"><rect x="3" y="0.5" width="6" height="11" rx="1" fill="var(--brand-orange)"/><rect x="4" y="2" width="4" height="7" fill="#fff"/></svg>
          +41 79 402 61 57
        </li>
        <li>
          <svg viewBox="0 0 12 12"><rect x="0.5" y="2" width="11" height="8" rx="1" fill="var(--brand-orange)"/><path d="M1 2.5l5 4 5-4" fill="none" stroke="#fff" stroke-width="1"/></svg>
          lena.brandt@tallivo.ch
        </li>
        <li>
          <svg viewBox="0 0 12 12"><circle cx="6" cy="6" r="5" fill="none" stroke="var(--brand-orange)" stroke-width="1.3"/><path d="M1 6h10M6 1c-2.5 3-2.5 7 0 10M6 1c2.5 3 2.5 7 0 10" fill="none" stroke="var(--brand-orange)" stroke-width="1"/></svg>
          www.tallivo.com.au
        </li>
      </ul>
    </div>
  </section>
</body>
</html>
```